Business Card Design for Marketing Firm

Looking for business card design for higher end marketing firm. Clean but impressionable/trendy. We are a marketing firm that represents manufacturers in the foodservice equipment and supply industry. Our customers are end users such has hotels, restaurants, country clubs, convention centers and casinos as well as distributors of restaurants supplies and equipment, and manufacturers of foodservice equipment and supplies.
Target Market(s)
Hotels, Restaurants, Supply & Equipment Distributors, Foodservice Manufacturers
Industry/Entity Type
Foodservice/Hospitality
Contact Information for Business Card
Name, Title, Contact Number, Email, Website, Social Media, Address
Requirements
Must have
- Clean & Simple but Serious and Impressionable

```html
<!DOCTYPE html>
<html lang="en">
<head>
<meta charset="utf-8">
<title>Meridian Hospitality Reps – Business Card</title>
<link href="https://fonts.googleapis.com/css2?family=Cinzel:wght@600;700&family=Tinos:wght@400;700&display=swap" rel="stylesheet">
<style>
  :root {
    --brand-blue: #2c2a85;
    --paper: #ffffff;
    --ink: #1c1c28;
    --wave-grey: #c4c4c8;
    --backdrop: #e9e9ec;
  }
  * { box-sizing: border-box; margin: 0; padding: 0; }
  html, body { width: 1200px; height: 900px; overflow: hidden; }
  body {
    background: var(--backdrop);
    display: flex; flex-direction: column; align-items: center; justify-content: center;
    gap: 56px;
  }
  .card {
    position: relative;
    width: 640px; height: 366px;
    border-radius: 26px;
    overflow: hidden;
    box-shadow: 0 6px 18px rgba(0,0,0,.18);
  }
  .card--front { background: var(--brand-blue); color: var(--paper); }
  .card--back { background: var(--paper); color: var(--ink); }

  .brand {
    position: absolute;
    font-family: "Cinzel", serif;
    font-weight: 700;
    text-transform: uppercase;
    line-height: 1.05;
  }
  .card--front .brand {
    left: 0; right: 0; top: 118px; text-align: center;
    font-size: 40px; letter-spacing: 2px; color: var(--paper);
  }
  .card--front .brand-rule {
    position: absolute; left: 150px; right: 150px; top: 244px;
    height: 2px; background: var(--paper);
  }
  .brand-dot {
    display: inline-block; width: 16px; height: 16px; border-radius: 50%;
    background: currentColor; vertical-align: middle; margin-right: 12px;
    position: relative; top: -4px;
  }

  .card--back .wave { position: absolute; left: 0; top: 0; width: 640px; height: 366px; }
  .card--back .brand {
    left: 30px; top: 108px; width: 280px; text-align: center;
    font-size: 26px; letter-spacing: 1px; color: var(--brand-blue);
  }
  .card--back .brand-rule {
    position: absolute; left: 50px; width: 240px; top: 184px;
    height: 1.5px; background: var(--brand-blue);
  }
  .divider {
    position: absolute; left: 330px; top: 40px; height: 180px; width: 1.5px;
    background: var(--brand-blue);
  }
  .contact {
    position: absolute; left: 348px; top: 30px;
    font-family: "Tinos", serif; font-size: 14px; line-height: 1.35; color: var(--ink);
  }
  .contact .name {
    font-family: "Cinzel", serif; font-weight: 700; font-size: 22px;
    color: var(--brand-blue); letter-spacing: 1px;
  }
  .contact .title { margin-bottom: 6px; }
  .contact .address { margin-bottom: 6px; }
  .contact .row { display: flex; align-items: center; gap: 8px; }
  .contact svg { flex: none; }
  .social-dots { display: flex; gap: 4px; }
  .social-dots span {
    width: 13px; height: 13px; border-radius: 50%; background: var(--brand-blue); display: block;
  }
</style>
</head>
<body>

<section class="card card--front" aria-label="Card front">
  <h1 class="brand"><span class="brand-dot"></span>Meridian<br>Hospitality Reps</h1>
  <div class="brand-rule"></div>
</section>

<section class="card card--back" aria-label="Card back">
  <svg class="wave" viewBox="0 0 640 366" aria-hidden="true">
    <path d="M0 334 C 200 330, 320 318, 420 282 C 500 254, 570 244, 640 240" fill="none" stroke="var(--wave-grey)" stroke-width="6"/>
    <path d="M0 344 C 200 340, 325 326, 428 290 C 505 262, 572 252, 640 248 L640 366 L0 366 Z" fill="var(--brand-blue)"/>
  </svg>

  <h2 class="brand">Meridian<br>Hospitality Reps</h2>
  <div class="brand-rule"></div>
  <div class="divider"></div>

  <div class="contact">
    <div class="name">Daniel Harlow</div>
    <div class="title">Co-Founder</div>
    <div class="address">P.O. BOX 45-12 NTH-30<br>Cedar Lane 14, Fairview</div>
    <div class="row">
      <svg width="14" height="14" viewBox="0 0 24 24" fill="var(--brand-blue)" aria-hidden="true"><path d="M6.6 10.8a15 15 0 0 0 6.6 6.6l2.2-2.2a1 1 0 0 1 1-.25 11.4 11.4 0 0 0 3.6.57 1 1 0 0 1 1 1V20a1 1 0 0 1-1 1A17 17 0 0 1 3 4a1 1 0 0 1 1-1h3.5a1 1 0 0 1 1 1c0 1.25.2 2.45.57 3.57a1 1 0 0 1-.25 1z"/></svg>
      <span>555-014-2368</span>
    </div>
    <div class="row">
      <svg width="14" height="14" viewBox="0 0 24 24" fill="var(--brand-blue)" aria-hidden="true"><path d="M2 5h20v14H2z M3 6l9 7 9-7" stroke="#fff" stroke-width="1.5"/></svg>
      <span>info@meridianreps.com</span>
    </div>
    <div class="row">
      <svg width="14" height="14" viewBox="0 0 24 24" aria-hidden="true"><circle cx="12" cy="12" r="10" fill="var(--brand-blue)"/><path d="M2 12h20M12 2c3 3 3 17 0 20M12 2c-3 3-3 17 0 20" stroke="#fff" stroke-width="1.3" fill="none"/></svg>
      <span>www.meridianreps.com</span>
    </div>
    <div class="row">
      <div class="social-dots" aria-hidden="true"><span></span><span></span><span></span><span></span></div>
      <span>@meridianreps</span>
    </div>
  </div>
</section>

</body>
</html>
```